Mindfulness School for Children -- Business Cards

We're looking for business cards for our school directors and owners. We're a mindfulness school for children called little lanterns. Attached are our logos/icons.

```html
<!DOCTYPE html>
<html lang="en">
<head>
<meta charset="utf-8">
<title>little lanterns — Business Cards</title>
<link rel="stylesheet" href="https://fonts.googleapis.com/css2?family=Alegreya:wght@500&family=Arimo:wght@400;700&display=swap">
<style>
  :root {
    --backdrop: #1f1f1f;
    --card-light: #8fd0dd;
    --card-mid: #6cc0d2;
    --card-deep: #4fb3c9;
    --ink: #ffffff;
  }
  * { margin: 0; padding: 0; box-sizing: border-box; }
  html, body {
    width: 1200px; height: 1059px; overflow: hidden;
    background: var(--backdrop);
  }
  .canvas { position: relative; width: 1200px; height: 1059px; }
  .card {
    position: absolute;
    overflow: hidden;
    box-shadow: 0 14px 28px rgba(0,0,0,0.6);
    color: var(--ink);
  }
  .card-texture {
    position: absolute; inset: 0;
    background:
      radial-gradient(ellipse at 70% 15%, var(--card-deep) 0%, transparent 45%),
      radial-gradient(ellipse at 20% 30%, var(--card-mid) 0%, transparent 55%),
      linear-gradient(180deg, var(--card-mid) 0%, var(--card-light) 100%);
  }
  .card-front { left: 256px; top: 89px; width: 688px; height: 390px; }
  .card-back  { left: 253px; top: 546px; width: 694px; height: 395px; }

  .brand-name {
    position: absolute;
    font-family: "Alegreya", Georgia, serif;
    font-weight: 500;
    color: var(--ink);
    white-space: nowrap;
    letter-spacing: 0.5px;
  }
  .card-front .brand-name { left: 49px; top: 183px; width: 286px; text-align: center; font-size: 40px; }
  .card-back .brand-name { left: 0; right: 0; top: 176px; text-align: center; font-size: 72px; }

  .divider {
    position: absolute; left: 363px; top: 110px;
    width: 1px; height: 172px; background: var(--ink);
  }
  .contact {
    position: absolute; left: 389px; top: 108px;
    font-family: "Arimo", Arial, sans-serif;
  }
  .person-name { font-size: 23px; font-weight: 700; line-height: 26px; }
  .person-role { font-size: 15.5px; line-height: 20px; }
  .address { margin-top: 12px; font-size: 15.5px; line-height: 19.5px; }
  .contact-list { list-style: none; margin-top: 11px; font-size: 15.5px; }
  .contact-list li { display: flex; align-items: center; height: 25px; }
  .contact-list svg { width: 11px; height: 11px; margin-right: 7px; fill: var(--ink); flex: none; }
</style>
</head>
<body>
<main class="canvas">
  <section class="card card-front">
    <div class="card-texture" role="img" aria-label="Soft turquoise watercolour wash background"></div>
    <div class="brand-name">little lanterns</div>
    <div class="divider"></div>
    <div class="contact">
      <p class="person-name">DANIEL HAYES</p>
      <p class="person-role">CEO/Founder</p>
      <p class="address">Po Box 4120 Elm Street<br>Country Name, AB 62318</p>
      <ul class="contact-list">
        <li><svg viewBox="0 0 12 12" aria-hidden="true"><path d="M2.5 0.5 L4.5 0.5 L5.2 3.2 L3.8 4.3 C4.5 6 6 7.5 7.7 8.2 L8.8 6.8 L11.5 7.5 L11.5 9.5 C11.5 10.6 10.6 11.5 9.5 11.5 C4.5 11.2 0.8 7.5 0.5 2.5 C0.5 1.4 1.4 0.5 2.5 0.5 Z"/></svg>(00) 5283 9164</li>
        <li><svg viewBox="0 0 12 12" aria-hidden="true"><path d="M0 2 H12 V10 H0 Z M0.8 2.6 L6 6.6 L11.2 2.6 V3.6 L6 7.6 L0.8 3.6 Z" fill-rule="evenodd"/></svg>info@littlelanterns.com</li>
        <li><svg viewBox="0 0 12 12" aria-hidden="true"><circle cx="6" cy="6" r="5.5"/><path d="M3 3.5 C4.5 3 5.5 4.5 4.5 5.5 C3.5 6.5 4.5 8 5 9.5 M8 2.5 C7 4 8.5 5 9.5 5.5" stroke="var(--card-mid)" stroke-width="1.2" fill="none"/></svg>www.littlelanterns.com</li>
      </ul>
    </div>
  </section>

  <section class="card card-back">
    <div class="card-texture" role="img" aria-label="Soft turquoise watercolour wash background"></div>
    <div class="brand-name">little lanterns</div>
  </section>
</main>
</body>
</html>
```